CREATE A 2 layout and logo ( servanilo )

I need to create 2 layout for my company being a homepage will be like and other client control panel and need to create the logo of the company, my company works with website hosting and sale of dedicated server and VPS cloud the company name and servanilo, I want the site to be very accessible and that is not too flashy

Target Market(s)

website hosting

Industry/Entity Type

It Company

Number of Pages Required

2 page

Font styles to use
Sans Serif

Requirements
Must have
• domain servanilo.example
Nice to have
• banners, login area, login webmail
Should not have
• no preference

```html
<!DOCTYPE html>
<html lang="en">
<head>
<meta charset="utf-8">
<title>Servanilo — Hosting, Dedicated Servers, VPS Cloud</title>
<link rel="stylesheet" href="https://fonts.googleapis.com/css2?family=Arimo:wght@700&family=Open+Sans:ital,wght@0,400;0,600;1,400&display=swap">
<style>
:root{
  --brand:#2249a0;
  --brand-dark:#1e4396;
  --heading:#2a4f9c;
  --ink:#444;
  --muted:#8a8a8a;
  --nav-active:#2b2b2b;
  --panel:#333;
  --panel-deep:#1b1b1b;
  --field:#ececec;
  --white:#fff;
}
*{box-sizing:border-box;margin:0;padding:0}
html,body{width:670px;height:1200px;overflow:hidden;background:var(--white)}
body{position:relative;font-family:"Open Sans",Arial,sans-serif;color:var(--ink)}
.abs{position:absolute}

/* header */
.logo{left:56px;top:6px;font-family:"Arimo",Arial,sans-serif;font-weight:700;font-size:24px;color:var(--brand);letter-spacing:-.2px}
.btn-sm{top:14px;height:16px;font-size:6.5px;color:var(--white);border-radius:2px;display:flex;align-items:center;justify-content:center}
.btn-register{left:499px;width:39px;background:var(--brand)}
.btn-login{left:542px;width:34px;background:#2f2f2f}
.lang{top:18px;width:11px;height:8px;border:1px solid #ccc}
.lang-en{left:587px;background:#d9dde8}
.lang-pt{left:602px;background:#7aa35a}

/* nav */
.nav{left:0;top:45px;width:670px;height:25px;background:var(--brand)}
.nav-item{top:0;height:25px;display:flex;align-items:center;justify-content:center;font-size:6.8px;font-weight:600;color:var(--white);border-right:1px solid rgba(255,255,255,.18)}
.nav-item.active{background:var(--nav-active)}

/* hero */
.hero{left:0;top:70px;width:670px;height:232px;background:linear-gradient(180deg,#e9e9e9 0%,#c9c9c9 45%,#e4e4e4 100%)}
.hero-arrow{top:176px;width:15px;height:19px;background:#8d8d8d;display:flex;align-items:center;justify-content:center}

/* welcome */
.welcome-title{left:64px;top:338px;font-size:16px;color:var(--heading);font-weight:400}
.welcome-text{left:64px;top:364px;width:330px;font-size:6.3px;line-height:11.4px;color:#555}
.login-title{left:64px;top:432px;font-size:9px;color:var(--heading)}
.field{top:450px;height:21px;background:var(--field);border:1px solid #e0e0e0;font-size:6px;color:#666;padding-left:7px;display:flex;align-items:center}
.btn-submit{left:323px;top:450px;width:42px;height:21px;background:linear-gradient(#9a9a9a,#7a7a7a);color:var(--white);font-size:6.5px;font-weight:600;display:flex;align-items:center;justify-content:center}
.welcome-photo{left:409px;top:342px;width:199px;height:131px;background:linear-gradient(135deg,#4a5e70,#8aa0a8 55%,#3c4a55)}

/* services */
.services{left:0;top:514px;width:670px;height:222px;background:var(--brand)}
.services-title{left:0;top:540px;width:670px;text-align:center;font-size:15px;font-weight:600;color:var(--white)}
.service{top:580px;width:170px;text-align:center;color:var(--white)}
.service-icon{width:60px;height:60px;margin:0 auto;border-radius:50%;background:var(--white);display:flex;align-items:center;justify-content:center}
.service-name{margin-top:7px;font-size:11.5px;font-weight:600}
.service-text{margin-top:4px;font-size:6px;line-height:10.4px}

/* clients */
.clients-label{left:0;top:769px;width:670px;text-align:center;font-size:6px;color:var(--muted)}
.client{top:792px;font-size:8.5px;font-weight:600;color:#555;transform:translateX(-50%);white-space:nowrap}

/* testimonials */
.testi-title{left:0;top:837px;width:670px;text-align:center;font-size:12.5px;font-weight:600;color:var(--heading)}
.testi-photo{left:86px;top:867px;width:86px;height:86px;border-radius:50%;background:linear-gradient(160deg,#c9a48c,#7a5a48)}
.testi-name{left:181px;top:865px;font-size:8.5px;color:#333}
.testi-name small{font-size:6px;color:#666}
.testi-rule{left:181px;top:880px}
.testi-quote{left:181px;top:902px;width:405px;font-size:6.7px;line-height:14.5px;font-style:italic;color:#777}
.q{font-style:normal;font-weight:600;font-size:13px;color:#888;vertical-align:-3px}

/* footer */
.footer{left:0;top:984px;width:670px;height:166px;background:var(--panel)}
.news-title{left:66px;top:999px;font-size:19px;color:var(--white);font-weight:400}
.news-field{top:1006px;height:15px;background:var(--white);font-size:6px;color:#333;padding-left:8px;display:flex;align-items:center}
.btn-subscribe{left:561px;top:1006px;width:45px;height:15px;background:#8a8a8a;color:var(--white);font-size:6.5px;font-weight:600;display:flex;align-items:center;justify-content:center}
.rule-h{left:56px;top:1043px;width:560px;height:1px;background:#555}
.rule-v{top:1064px;width:1px;height:70px;background:#555}
.col-title{top:1062px;font-size:9.5px;color:var(--white)}
.news-list{left:56px;top:1081px;width:165px;list-style:none;font-size:5.8px;line-height:9px;color:#ccc}
.news-list li{position:relative;padding-left:10px;margin-bottom:4px}
.news-list li::before{content:"•";position:absolute;left:3px}
.links{top:1082px;list-style:none;font-size:5.5px;color:#aaa;line-height:13.3px}
.links li::before{content:"• ";}
.social{width:14px;height:14px;border-radius:50%}
.bottom{left:0;top:1150px;width:670px;height:50px;background:var(--panel-deep)}
.copy{left:57px;top:1163px;font-size:5.3px;color:#888}
.legal{left:57px;top:1178px;font-size:5.3px;color:#888}
.round{top:1167px;width:16px;height:16px;border-radius:50%;border:1px solid #bbb;display:flex;align-items:center;justify-content:center}
</style>
</head>
<body>

<header>
  <div class="abs logo">Servanilo</div>
  <div class="abs btn-sm btn-register">Register</div>
  <div class="abs btn-sm btn-login">Log in</div>
  <div class="abs lang lang-en" role="img" aria-label="English language"></div>
  <div class="abs lang lang-pt" role="img" aria-label="Portuguese language"></div>
</header>

<nav class="abs nav">
  <div class="abs nav-item active" style="left:54px;width:97px">HOME</div>
  <div class="abs nav-item" style="left:151px;width:112px">ABOUT US</div>
  <div class="abs nav-item" style="left:263px;width:107px">SERVICES</div>
  <div class="abs nav-item" style="left:370px;width:128px">TESTIMONIALS</div>
  <div class="abs nav-item" style="left:498px;width:116px">CONTACT US</div>
</nav>

<section class="abs hero" role="img" aria-label="Bright white data centre hall with rows of server racks"></section>
<div class="abs hero-arrow" style="left:0">
  <svg width="6" height="10" viewBox="0 0 6 10"><path d="M5 1 1 5l4 4" fill="none" stroke="#fff" stroke-width="1.2"/></svg>
</div>
<div class="abs hero-arrow" style="left:655px">
  <svg width="6" height="10" viewBox="0 0 6 10"><path d="M1 1l4 4-4 4" fill="none" stroke="#fff" stroke-width="1.2"/></svg>
</div>

<section>
  <h1 class="abs welcome-title">Welcome to Servanilo</h1>
  <p class="abs welcome-text">Pellentesque convallis molestie enim sit amet efficitur. Etiam id imperdiet lectus. Vivamus lacus justo, ultrices nec erat in, euismod iaculis mauris. Vivamus eleifend vitae nulla vel malesuada. In ac malesuada lacus, et consectetur ante. Fusce vitae lectus sit amet mi pulvinar maximus. Aenean placerat, nibh vel accumsan aliquet, magna nibh accumsan nibh, ac tempus nunc ipsum ac tellus. Cras augue magna, placerat eget nulla non, congue suscipit neque. Nunc sit amet consequat risus.</p>
  <h2 class="abs login-title">Member Login</h2>
  <div class="abs field" style="left:64px;width:123px">Name</div>
  <div class="abs field" style="left:194px;width:123px">E-mail</div>
  <div class="abs btn-submit">SUBMIT</div>
  <div class="abs welcome-photo" role="img" aria-label="Two technicians checking a server rack with a laptop"></div>
</section>

<section class="abs services"></section>
<h2 class="abs services-title">Our Services</h2>
<div class="abs service" style="left:54px">
  <div class="service-icon">
    <svg width="18" height="20" viewBox="0 0 18 20"><g fill="var(--brand)"><ellipse cx="9" cy="3.5" rx="8" ry="3"/><path d="M1 6c0 1.7 3.6 3 8 3s8-1.3 8-3v3.5c0 1.7-3.6 3-8 3s-8-1.3-8-3z"/><path d="M1 12c0 1.7 3.6 3 8 3s8-1.3 8-3v4c0 1.7-3.6 3-8 3s-8-1.3-8-3z"/></g></svg>
  </div>
  <div class="service-name">Website Hosting</div>
  <p class="service-text">Aenean sed quam non sapien faucibus consequat vitae sit amet orci. Praesent quis risus mi. In mollis nulla in pulvinar dictum.</p>
</div>
<div class="abs service" style="left:245px">
  <div class="service-icon">
    <svg width="18" height="14" viewBox="0 0 18 14"><path d="M4 1h10l3 6v5H1V7z" fill="none" stroke="var(--brand)" stroke-width="1.6"/><path d="M1 7h16" stroke="var(--brand)" stroke-width="1.4"/><circle cx="13" cy="9.8" r="1" fill="var(--brand)"/></svg>
  </div>
  <div class="service-name">Dedicated Servers</div>
  <p class="service-text">Aenean sed quam non sapien faucibus consequat vitae sit amet orci. Praesent quis risus mi. In mollis nulla in pulvinar dictum.</p>
</div>
<div class="abs service" style="left:437px">
  <div class="service-icon">
    <svg width="22" height="15" viewBox="0 0 22 15"><path d="M5 15a5 5 0 0 1-.6-10A6.5 6.5 0 0 1 16.5 4 5.5 5.5 0 0 1 17 15z" fill="var(--brand)"/></svg>
  </div>
  <div class="service-name">VPS cloud</div>
  <p class="service-text">Aenean sed quam non sapien faucibus consequat vitae sit amet orci. Praesent quis risus mi. In mollis nulla in pulvinar dictum.</p>
</div>

<section>
  <div class="abs clients-label">CLIENTS</div>
  <div class="abs client" style="left:96px">Fernbrook</div>
  <div class="abs client" style="left:161px">Quillora</div>
  <div class="abs client" style="left:225px">Linkvale</div>
  <div class="abs client" style="left:285px">Sorrel</div>
  <div class="abs client" style="left:346px">Kyrona</div>
  <div class="abs client" style="left:410px">Tevo</div>
  <div class="abs client" style="left:475px">Micraline</div>
  <div class="abs client" style="left:537px">Adra</div>
  <div class="abs client" style="left:582px">Cirvo</div>
</section>

<section>
  <h2 class="abs testi-title">TESTIMONIALS</h2>
  <div class="abs testi-photo" role="img" aria-label="Portrait of the client Olivia"></div>
  <div class="abs testi-name">Olivia, <small>Company Name</small></div>
  <svg class="abs testi-rule" width="406" height="10" viewBox="0 0 406 10">
    <path d="M0 6.5h25l7 6 7-6h367" fill="none" stroke="#ccc" stroke-width="1"/>
  </svg>
  <p class="abs testi-quote"><span class="q">“</span> Aenean aliquet risus metus, vitae tristique enim finibus eu. Sed iaculis nisl est, vitae sagittis risus fermentum sed. Donec lobortis, dui sed eleifend pellentesque, erat dui tincidunt urna, eu eleifend ante felis quis enim. Nam et turpis non turpis cursus rhoncus a et urna. Nunc tristique nec tortor vitae imperdiet. <span class="q">”</span></p>
</section>

<footer>
  <div class="abs footer"></div>
  <h2 class="abs news-title">News Letter</h2>
  <div class="abs news-field" style="left:180px;width:120px">First name</div>
  <div class="abs news-field" style="left:307px;width:121px">Last name</div>
  <div class="abs news-field" style="left:434px;width:121px">Email ID</div>
  <div class="abs btn-subscribe">Subscribe</div>
  <div class="abs rule-h"></div>

  <h3 class="abs col-title" style="left:56px">Latest news</h3>
  <ul class="abs news-list">
    <li>Phasellus nisl est, condimentum vitae faucibus in, sollicitudin vel metus</li>
    <li>Sed libero felis, vestibulum et dolor eget, lacinia aliquet neque.</li>
    <li>Aenean sed quam non sapien faucibus</li>
  </ul>
  <div class="abs rule-v" style="left:234px"></div>

  <h3 class="abs col-title" style="left:262px">Quick Links</h3>
  <ul class="abs links" style="left:263px"><li>Home</li><li>About us</li><li>Services</li><li>Testimonials</li></ul>
  <ul class="abs links" style="left:340px"><li>Aliquam ac elit</li><li>Nulla ut</li><li>Proin ut enim</li><li>Donec aliquam</li></ul>
  <ul class="abs links" style="left:426px"><li>Aliquam dignissim</li><li>Nulla porttitor nibh</li><li>Duis hendrerit arcu</li><li>Dam elementum velit</li></ul>
  <div class="abs rule-v" style="left:516px"></div>

  <h3 class="abs col-title" style="left:542px;top:1063px">Follow us on</h3>
  <div class="abs social" style="left:543px;top:1083px;background:#3b5998"></div>
  <div class="abs social" style="left:562px;top:1083px;background:#2ea0dc"></div>
  <div class="abs social" style="left:582px;top:1083px;background:#3a3a3a"></div>
  <div class="abs social" style="left:601px;top:1083px;background:#c8202c"></div>
  <div class="abs social" style="left:543px;top:1103px;background:#f06a20"></div>
  <div class="abs social" style="left:562px;top:1103px;background:#d12a24"></div>
  <div class="abs social" style="left:582px;top:1103px;background:#5aa23a"></div>

  <div class="abs bottom"></div>
  <div class="abs copy">Copyright © 2015 Servanilo. All Rights Reserved.</div>
  <div class="abs legal">Terms of Use | Legal Disclaimer | Privacy Policy | Sitemap</div>
  <div class="abs round" style="left:578px">
    <svg width="8" height="6" viewBox="0 0 8 6"><rect x=".5" y=".5" width="7" height="5" fill="none" stroke="#ddd" stroke-width=".8"/><path d="M.5.5 4 3.5 7.5.5" fill="none" stroke="#ddd" stroke-width=".8"/></svg>
  </div>
  <div class="abs round" style="left:598px">
    <svg width="8" height="8" viewBox="0 0 8 8"><path d="M4 7V1M1 4l3-3 3 3" fill="none" stroke="#ddd" stroke-width="1"/></svg>
  </div>
</footer>

</body>
</html>
```